Pinecrest Capital Group - Company Envelopes

I am looking for a graphic designer to create a bespoke envelope for my company use, which I can then have printed at scale. The envelope should be of standard size and shape, but Matt black in colour, with semi-thick vertical gloss (shiny) lines going from left to right, but must stop to the right of the envelope, leaving a Matt black line with enough space for a stamp in the top right corner. The back of the envelope should be full Matt black.

Requirements
Must have
• Must be as described in brief
Should not have
• No other colours - Just Matt and Gloss Black

```html
<!DOCTYPE html>
<html lang="en">
<head>
<meta charset="utf-8">
<title>Pinecrest Capital Group – Company Envelopes</title>
<style>
  :root {
    --backdrop: #c0c0c0;
    --matt-black: #222222;
    --gloss-light: #707070;
    --gloss-mid: #4a4a4a;
    --gloss-dark: #151515;
    --flap-edge: #d8d8d8;
  }
  html, body {
    margin: 0;
    padding: 0;
    width: 1200px;
    height: 895px;
    overflow: hidden;
    background: var(--backdrop);
  }
  .canvas {
    position: relative;
    width: 1200px;
    height: 895px;
  }
  .envelope {
    position: absolute;
    background: var(--matt-black);
  }
  .envelope--back {
    left: 285px;
    top: 135px;
    width: 629px;
    height: 275px;
  }
  .envelope__flap {
    position: absolute;
    left: 0;
    top: 0;
    width: 629px;
    height: 275px;
  }
  .envelope--front {
    left: 285px;
    top: 487px;
    width: 628px;
    height: 272px;
    overflow: hidden;
  }
  .gloss-stripe {
    position: absolute;
    top: 0;
    width: 25px;
    height: 100%;
  }
  .gloss-stripe--1 { left: 0;     background: linear-gradient(to bottom, var(--gloss-light) 0%, var(--gloss-light) 60%, #5c5c5c 100%); }
  .gloss-stripe--2 { left: 49px;  background: linear-gradient(to bottom, var(--gloss-light) 0%, var(--gloss-light) 45%, var(--gloss-mid) 100%); }
  .gloss-stripe--3 { left: 97px;  background: linear-gradient(to bottom, var(--gloss-light) 0%, var(--gloss-light) 35%, #333 100%); }
  .gloss-stripe--4 { left: 145px; background: linear-gradient(to bottom, var(--gloss-light) 0%, var(--gloss-light) 25%, #262626 100%); }
  .gloss-stripe--5 { left: 193px; background: linear-gradient(to bottom, var(--gloss-light) 0%, #5e5e5e 30%, var(--gloss-dark) 100%); }
  .stamp-area {
    position: absolute;
    left: 542px;
    top: 8px;
    width: 77px;
    height: 77px;
    background: linear-gradient(135deg, #8a8a8a 0%, #3a3a3a 30%, #111 55%, #0f1010 100%);
  }
</style>
</head>
<body>
<main class="canvas">
  <section class="envelope envelope--back" aria-label="Envelope back, full matt black">
    <svg class="envelope__flap" viewBox="0 0 629 275" xmlns="http://www.w3.org/2000/svg">
      <path d="M0 0 L21 82 Q27 101 48 101 L581 101 Q602 101 608 82 L629 1"
            fill="none" stroke="var(--flap-edge)" stroke-width="0.8"/>
    </svg>
  </section>

  <section class="envelope envelope--front" aria-label="Envelope front, matt black with gloss stripes">
    <div class="gloss-stripe gloss-stripe--1"></div>
    <div class="gloss-stripe gloss-stripe--2"></div>
    <div class="gloss-stripe gloss-stripe--3"></div>
    <div class="gloss-stripe gloss-stripe--4"></div>
    <div class="gloss-stripe gloss-stripe--5"></div>
    <div class="stamp-area" aria-label="Gloss stamp area"></div>
  </section>
</main>
</body>
</html>
```